Graphic Design for 2026 AGGMS Summit – 4:3 Ratio Event Image

The Allied Guild of Garment Makers and Suppliers (AGGMS) is seeking a high-quality, professional graphic to serve as the primary visual template for our 2026 AGGMS Summit & Showcase. This image will be used across digital, print, and on-site event materials. We need a visually striking, industry-relevant design that reflects the uniform, image apparel, and workwear industry and captures the spirit of innovation, networking, and global connection that defines our annual convention.

Key Details:
Event Name: 2026 AGGMS Summit & Showcase

Audience: Uniform manufacturers, distributors, and suppliers serving public safety, hospitality, healthcare, corporate, and industrial markets.

Purpose of Image:

Serve as the main branding graphic for the convention.

Be adaptable for use on our website, social media, email campaigns, signage, and printed materials.

Provide a modern, professional, future-focused look appealing to business decision-makers in the uniform and workwear sector.

Design Requirements:
Format: Layered file delivery (Adobe Illustrator or Photoshop).

If Photoshop, final file must be minimum 2500px wide for high-quality print output.

Aspect Ratio: 4:3 (landscape).

Style:

Clean, professional, and corporate.

Forward-looking, innovative feel (not dated or generic).

Should represent the diverse industries where uniforms are worn (public safety, healthcare, hospitality, industrial, corporate office).

Abstract or conceptual elements (e.g., flowing fabric, silhouettes of professionals, global connections) are welcome. Avoid clip-art or overly literal graphics.

Color Palette: Prefer use of AGGMS’s primary brand colors where possible:

Blue: #204295

Red: #EC1F25
Designers may incorporate complementary colors to enhance the look, but these two should be prominent.

Deliverables:
Main design file in Illustrator (.AI) or Photoshop (.PSD), layered and editable.

High-resolution exported version for immediate use.

Adaptable design suitable for other sizes and formats in future.

Inspiration:
We want a bold, memorable image that conveys:

The professionalism and scale of the uniform industry.

Innovation, progress, and networking.

Global reach and cross-industry connections fostered by AGGMS’s annual convention.

Usage Rights:
AGGMS will retain full rights to the final chosen design for unlimited future use across digital and print channels.

Attached is a rough concept I created. I’m not satisfied with it, but it shows the basic layout idea. I’d like you to take the concept to a much more professional, polished level, incorporating our brand colors (Blue #204295, Red #EC1F25) and a modern, corporate feel.

Requirements
Must have
• Include this text: Threads of Tomorrow: The Weave of Vision, Talent, and Promise AGGMS 2026 SUMMIT Uniform and Workwear Professionals

```html
<!DOCTYPE html>
<html lang="en">
<head>
<meta charset="utf-8">
<title>AGGMS 2026 Summit</title>
<link rel="stylesheet" href="https://fonts.googleapis.com/css2?family=Manrope:wght@400;500;700;800&display=swap">
<style>
  :root {
    --brand-blue: #204295;
    --brand-red: #EC1F25;
    --banner-red: #F4202F;
    --paper: #ffffff;
    --sky-top: #6aa6f2;
    --sky-mid: #c493e6;
    --tower-dark: #4a2430;
    --tower-glow: #7a3a3f;
  }
  * { margin: 0; padding: 0; box-sizing: border-box; }
  html, body { width: 1200px; height: 900px; overflow: hidden; background: var(--paper); }
  body { font-family: "Manrope", Arial, sans-serif; }
  .event-graphic { position: relative; width: 1200px; height: 900px; overflow: hidden; background: var(--paper); }

  .venue-photo {
    position: absolute; left: 440px; top: 0; width: 760px; height: 900px;
    background: linear-gradient(180deg, var(--sky-top) 0%, var(--sky-mid) 35%, var(--tower-glow) 55%, var(--tower-dark) 100%);
  }
  .white-field { position: absolute; left: 0; top: 0; width: 1200px; height: 900px; }

  .headline-block { position: absolute; left: 40px; top: 138px; color: var(--brand-blue); }
  .tagline {
    margin-left: 5px;
    font-size: 28px; font-weight: 700; color: var(--brand-red);
    letter-spacing: -0.2px; text-transform: uppercase;
  }
  .event-title {
    margin-top: 12px;
    font-size: 112px; font-weight: 700; line-height: 0.8; letter-spacing: -2px;
    text-transform: uppercase;
  }
  .event-title span { display: block; }
  .event-title span + span { margin-top: 10px; }
  .theme-title { margin-top: 38px; font-size: 68px; font-weight: 700; letter-spacing: -1px; line-height: 1; }
  .theme-subtitle { margin-top: 10px; font-size: 37px; font-weight: 400; letter-spacing: -0.4px; line-height: 1.1; }

  .info-banner {
    position: absolute; left: 38px; top: 597px; width: 953px; height: 268px;
    background: var(--banner-red); color: var(--paper);
    display: flex; align-items: center;
  }
  .info-date { width: 362px; text-align: center; }
  .info-date .dates { font-size: 32px; font-weight: 700; }
  .info-date .year { margin-top: 8px; font-size: 26px; font-weight: 500; }
  .info-divider { width: 1px; height: 166px; background: rgba(255,255,255,0.55); }
  .info-venue { flex: 1; text-align: center; }
  .info-venue .venue-name { font-size: 32px; font-weight: 700; }
  .info-venue .venue-address { margin-top: 10px; font-size: 25px; font-weight: 400; }

  .org-mark {
    position: absolute; left: 1005px; top: 648px; height: 166px;
    display: flex; align-items: center; padding-left: 20px;
    border-left: 1px solid rgba(255,255,255,0.7);
  }
  .org-mark span { font-size: 40px; font-weight: 800; color: var(--brand-red); }
</style>
</head>
<body>
  <main class="event-graphic">
    <div class="venue-photo" role="img" aria-label="Photo of the hotel tower lit at dusk against a blue and violet sky"></div>

    <svg class="white-field" viewBox="0 0 1200 900" aria-hidden="true">
      <path d="M0 0 H455 C700 0 853 180 853 430 V900 H0 Z" fill="var(--paper)"/>
    </svg>

    <section class="headline-block">
      <p class="tagline">Uniform and Workwear Professionals</p>
      <h1 class="event-title"><span>AGGMS 2026</span><span>SUMMIT</span></h1>
      <h2 class="theme-title">Threads of Tomorrow</h2>
      <p class="theme-subtitle">The Weave of Vision, Talent, and Promise</p>
    </section>

    <section class="info-banner">
      <div class="info-date">
        <p class="dates">May 03 – 05</p>
        <p class="year">2026</p>
      </div>
      <div class="info-divider"></div>
      <div class="info-venue">
        <p class="venue-name">Harborview Grand Plaza</p>
        <p class="venue-address">240 Meridian Ave, Harborview, MA 02199 USA</p>
      </div>
    </section>

    <div class="org-mark"><span>AGGMS</span></div>
  </main>
</body>
</html>
```